Trailer Lettering or Partial Wrap

I purchased a new gloss black 7' wide x 12' long x 7' height enclosed cargo trailer that I would like to brand for advertising. on all 4 sides. Our font is AgencyFB (and we only use lower case letters). To reduce cost I thought using the black gloss background could be achieved and use cut out vinyl rather than full wrap unless there are some other ideas. Our colors are Black, White, and Red (HEX #BE1E2D. Items to be displayed:
- logo
- phone # (405) 555-2716
- email. catering@kelpcornerok.com
- web address: www.kelpcornerok.com
- our 2 restaurant locations
- "Edmond" 4875 NE 92nd, Edmond OK 73099
- "NW-OKC" 2719 E Larkspur Ave, Oklahoma City, OK 73198

we would also like to highlight 3 services we offer:
- Catering
- Rent-A-Chef Events
- Sushi Making Classes

For reference our chopsticks from the logo files we use on a lot of print items. Not that I want it to be like this, but I did attach a sample of what ChatGPT created though is in an unusable format and fonts aren't consistent. As well a recent 2' x 4' sign we had made to use on table displays.

We also do like the wording on that last item of " Sushi | Experience | Elevated"

```html
<!DOCTYPE html>
<html lang="en">
<head>
<meta charset="utf-8">
<title>kelp corner – trailer lettering</title>
<link rel="stylesheet" href="https://fonts.googleapis.com/css2?family=Saira+Extra+Condensed:wght@300;400;600&display=swap">
<style>
  :root{
    --black:#000;
    --white:#fff;
    --red:#d90d12;
    --brand-red:#be1e2d;
    --door-gray:#c8c8c8;
    --door-edge:#9a9a9a;
    --page:#fff;
  }
  *{margin:0;padding:0;box-sizing:border-box}
  html,body{width:1200px;height:1001px;overflow:hidden;background:var(--page)}
  body{position:relative}
  .panel{position:absolute;display:block;background:var(--black)}
  .panel--front{left:34px;top:262px;width:233px;height:476px}
  .panel--side{left:294px;top:262px;width:872px;height:476px}
  .panel text{font-family:"Saira Extra Condensed","Arial Narrow",sans-serif;fill:var(--white);font-weight:300}
  .panel .brand-name{font-weight:600}
  .panel .loc-name,.panel .sep{fill:var(--red)}
  .panel .label{font-weight:400;text-anchor:middle}
  .rule{fill:var(--red)}
  .ring{fill:none;stroke:var(--white)}
  .door{fill:var(--door-gray);stroke:var(--door-edge);stroke-width:2}
  .door-inner{fill:var(--black)}
</style>
</head>
<body>
<svg width="0" height="0" style="position:absolute" aria-hidden="true">
  <defs>
    <symbol id="i-phone" viewBox="0 0 24 24"><path d="M7 4l3 4-2 2c1 2 3 4 5 5l2-2 4 3-2 3c-6 0-12-6-12-12z" fill="#d90d12"/></symbol>
    <symbol id="i-mail" viewBox="0 0 24 24"><rect x="5" y="7" width="14" height="10" fill="none" stroke="#d90d12" stroke-width="1.6"/><path d="M5 7l7 6 7-6" fill="none" stroke="#d90d12" stroke-width="1.6"/></symbol>
    <symbol id="i-web" viewBox="0 0 24 24"><g fill="none" stroke="#d90d12" stroke-width="1.5"><circle cx="12" cy="12" r="7"/><ellipse cx="12" cy="12" rx="3" ry="7"/><path d="M5 12h14M6.5 8.5h11M6.5 15.5h11"/></g></symbol>
    <symbol id="i-pin" viewBox="0 0 24 24"><path d="M12 4a5 5 0 0 0-5 5c0 4 5 10 5 10s5-6 5-10a5 5 0 0 0-5-5z" fill="#d90d12"/><circle cx="12" cy="9" r="2" fill="#000"/></symbol>
    <symbol id="i-cloche" viewBox="0 0 48 48"><g fill="none" stroke="#d90d12" stroke-width="2"><path d="M13 29a11 11 0 0 1 22 0z"/><path d="M10 31h28"/><circle cx="24" cy="16.5" r="1.5"/></g></symbol>
    <symbol id="i-chef" viewBox="0 0 48 48"><path d="M16 28c-4-1-5-6-2-8 1-4 6-5 8-3 2-3 6-3 8 0 3-2 7 0 7 4 2 3 1 6-3 7v5H16z" fill="none" stroke="#d90d12" stroke-width="3"/><path d="M16 33h16" stroke="#d90d12" stroke-width="3"/></symbol>
    <symbol id="i-rolls" viewBox="0 0 48 48"><g fill="none" stroke="#d90d12" stroke-width="1.6"><ellipse cx="17" cy="24" rx="6" ry="2.5"/><path d="M11 24v8c0 1.4 2.7 2.5 6 2.5s6-1.1 6-2.5v-8"/><ellipse cx="30" cy="19" rx="6" ry="2.5"/><path d="M24 19v9c0 1.4 2.7 2.5 6 2.5s6-1.1 6-2.5v-9"/><circle cx="17" cy="24" r="1"/><circle cx="30" cy="19" r="1"/></g></symbol>
  </defs>
</svg>

<!-- trailer front -->
<svg class="panel panel--front" viewBox="0 0 233 476" width="233" height="476">
  <circle cx="66" cy="98" r="6" fill="var(--red)"/>
  <text class="brand-name" x="78" y="94" font-size="34" textLength="44" lengthAdjust="spacingAndGlyphs">kelp</text>
  <text class="brand-name" x="78" y="126" font-size="34" textLength="72" lengthAdjust="spacingAndGlyphs">corner</text>

  <rect class="rule" x="24" y="179" width="185" height="1.5"/>
  <text x="28" y="208" font-size="17" textLength="178" lengthAdjust="spacingAndGlyphs">sushi <tspan class="sep">|</tspan> experience <tspan class="sep">|</tspan> elevated</text>
  <rect class="rule" x="24" y="227" width="185" height="1.5"/>

  <circle class="ring" cx="36" cy="255" r="8.5" stroke-width="2.2"/>
  <use href="#i-phone" x="28" y="247" width="16" height="16"/>
  <text x="51" y="260" font-size="16" textLength="89" lengthAdjust="spacingAndGlyphs">(405) 555-2716</text>
  <circle class="ring" cx="36" cy="281" r="8.5" stroke-width="2.2"/>
  <use href="#i-mail" x="28" y="273" width="16" height="16"/>
  <text x="51" y="286" font-size="16" textLength="155" lengthAdjust="spacingAndGlyphs">catering@kelpcornerok.com</text>
  <circle class="ring" cx="36" cy="307" r="8.5" stroke-width="2.2"/>
  <use href="#i-web" x="28" y="299" width="16" height="16"/>
  <text x="51" y="312" font-size="16" textLength="101" lengthAdjust="spacingAndGlyphs">kelpcornerok.com</text>
  <rect class="rule" x="24" y="333" width="185" height="1.5"/>

  <circle class="ring" cx="44" cy="374" r="18" stroke-width="4"/>
  <use href="#i-cloche" x="26" y="356" width="36" height="36"/>
  <text class="label" x="44" y="404" font-size="10" textLength="32" lengthAdjust="spacingAndGlyphs">catering</text>
  <rect class="rule" x="79" y="352" width="1.5" height="62"/>
  <circle class="ring" cx="116" cy="375" r="18" stroke-width="1.8"/>
  <use href="#i-rolls" x="98" y="357" width="36" height="36"/>
  <text class="label" x="116" y="404" font-size="10" textLength="49" lengthAdjust="spacingAndGlyphs">sushi making</text>
  <text class="label" x="116" y="414" font-size="10" textLength="28" lengthAdjust="spacingAndGlyphs">classes</text>
  <rect class="rule" x="151" y="352" width="1.5" height="62"/>
  <circle class="ring" cx="184" cy="375" r="18" stroke-width="1.8"/>
  <use href="#i-chef" x="166" y="357" width="36" height="36"/>
  <text class="label" x="184" y="404" font-size="10" textLength="44" lengthAdjust="spacingAndGlyphs">rent-a-chef</text>
  <text class="label" x="184" y="414" font-size="10" textLength="25" lengthAdjust="spacingAndGlyphs">events</text>
</svg>

<!-- trailer side -->
<svg class="panel panel--side" viewBox="0 0 872 476" width="872" height="476">
  <circle cx="70" cy="150" r="10" fill="var(--red)"/>
  <text class="brand-name" x="88" y="142" font-size="62" textLength="80" lengthAdjust="spacingAndGlyphs">kelp</text>
  <text class="brand-name" x="88" y="198" font-size="62" textLength="128" lengthAdjust="spacingAndGlyphs">corner</text>

  <circle class="ring" cx="284" cy="92" r="13" stroke-width="2.6"/>
  <use href="#i-phone" x="272" y="80" width="24" height="24"/>
  <text x="306" y="102" font-size="27" textLength="134" lengthAdjust="spacingAndGlyphs">(405) 555-2716</text>
  <circle class="ring" cx="284" cy="132" r="13" stroke-width="2.6"/>
  <use href="#i-mail" x="272" y="120" width="24" height="24"/>
  <text x="306" y="142" font-size="27" textLength="237" lengthAdjust="spacingAndGlyphs">catering@kelpcornerok.com</text>
  <circle class="ring" cx="284" cy="171" r="13" stroke-width="2.6"/>
  <use href="#i-web" x="272" y="159" width="24" height="24"/>
  <text x="306" y="181" font-size="27" textLength="154" lengthAdjust="spacingAndGlyphs">kelpcornerok.com</text>
  <rect class="rule" x="270" y="207" width="283" height="1.5"/>

  <circle class="ring" cx="284" cy="239" r="13" stroke-width="2.6"/>
  <use href="#i-pin" x="272" y="227" width="24" height="24"/>
  <text class="loc-name" x="306" y="245" font-size="18" textLength="43" lengthAdjust="spacingAndGlyphs">Edmond</text>
  <text x="306" y="265" font-size="18" textLength="181" lengthAdjust="spacingAndGlyphs">4875 NE 92nd, Edmond OK 73099</text>
  <circle class="ring" cx="284" cy="290" r="13" stroke-width="2.6"/>
  <use href="#i-pin" x="272" y="278" width="24" height="24"/>
  <text class="loc-name" x="306" y="298" font-size="18" textLength="45" lengthAdjust="spacingAndGlyphs">NW-OKC</text>
  <text x="306" y="319" font-size="18" textLength="254" lengthAdjust="spacingAndGlyphs">2719 E Larkspur Ave, Oklahoma City, OK 73198</text>
  <rect class="rule" x="270" y="335" width="289" height="1.5"/>
  <text x="279" y="376" font-size="30" textLength="273" lengthAdjust="spacingAndGlyphs">sushi <tspan class="sep">|</tspan> experience <tspan class="sep">|</tspan> elevated</text>
  <rect class="rule" x="270" y="400" width="289" height="1.5"/>

  <rect class="door" x="604" y="73" width="192" height="381"/>
  <rect class="door-inner" x="618" y="88" width="164" height="352"/>

  <circle class="ring" cx="703" cy="180" r="23" stroke-width="4"/>
  <use href="#i-cloche" x="680" y="157" width="46" height="46"/>
  <text class="label" x="703" y="221" font-size="15" textLength="42" lengthAdjust="spacingAndGlyphs">catering</text>
  <rect class="rule" x="672" y="231" width="60" height="2"/>
  <circle class="ring" cx="703" cy="268" r="23" stroke-width="2.4"/>
  <use href="#i-chef" x="680" y="245" width="46" height="46"/>
  <text class="label" x="703" y="305" font-size="15" textLength="58" lengthAdjust="spacingAndGlyphs">rent-a-chef</text>
  <text class="label" x="703" y="318" font-size="15" textLength="34" lengthAdjust="spacingAndGlyphs">events</text>
  <rect class="rule" x="672" y="327" width="60" height="2"/>
  <circle class="ring" cx="703" cy="363" r="23" stroke-width="2.4"/>
  <use href="#i-rolls" x="680" y="340" width="46" height="46"/>
  <text class="label" x="703" y="406" font-size="15" textLength="66" lengthAdjust="spacingAndGlyphs">sushi making</text>
  <text class="label" x="703" y="420" font-size="15" textLength="38" lengthAdjust="spacingAndGlyphs">classes</text>
</svg>
</body>
</html>
```